Otter Bites Guild - A Monthly Subscription Dog Treats Club - Shopify Website Design

A monthly subscription company. Need a Shopify Website Design and uploaded to fully work with Crisp Renewals.

Please look at these sites for examples as well as the images I enclosed.

https://www.mealbrightly.com/
https://www.globalmunchbox.com/

Number of Pages Required

1 page

```html
<!DOCTYPE html>
<html lang="en">
<head>
<meta charset="utf-8">
<title>Otter Bites Guild</title>
<link rel="stylesheet" href="https://fonts.googleapis.com/css2?family=Mulish:wght@400;600;700;800&display=swap">
<style>
  :root {
    --ink: #111111;
    --nav-bg: #1c1c1c;
    --footer-bg: #2b2b2b;
    --orange: #e0531c;
    --orange-soft: #f0a27f;
    --panel: #efefef;
    --card: #e9e9e9;
    --text: #444444;
    --muted: #cfcfcf;
    --trail: #c8c8c8;
    --white: #ffffff;
  }
  * { box-sizing: border-box; margin: 0; padding: 0; }
  html, body { width: 1200px; height: 3781px; overflow: hidden; }
  body { font-family: "Mulish", sans-serif; color: var(--ink); background: var(--white); position: relative; }
  section, header, footer { position: relative; width: 1200px; overflow: hidden; }
  .abs { position: absolute; }

  /* Navigation */
  .site-nav { height: 68px; background: var(--nav-bg); }
  .brand { left: 169px; top: 20px; font-size: 25px; font-weight: 800; color: var(--white); letter-spacing: 1px; text-transform: uppercase; }
  .menu { left: 474px; top: 24px; display: flex; gap: 40px; list-style: none; font-size: 15px; color: var(--white); }
  .menu .active { color: var(--orange); }
  .nav-icons { left: 964px; top: 26px; display: flex; gap: 10px; }

  /* Hero */
  .hero { height: 614px; background: linear-gradient(100deg, #5d4a3a 0%, #a47650 30%, #8a7a68 55%, #6f655d 80%, #4d4844 100%); }
  .hero-title { left: 795px; top: 240px; font-size: 74px; line-height: 98px; font-weight: 800; color: var(--white); text-transform: uppercase; }
  .hero-arrow { top: 348px; }

  /* Subscriptions */
  .subscriptions { height: 600px; text-align: center; }
  .section-title { font-size: 38px; font-weight: 600; }
  .subscriptions .section-title { position: absolute; top: 84px; width: 100%; }
  .subscriptions .lead { position: absolute; top: 150px; left: 225px; width: 750px; font-size: 14.5px; line-height: 22px; color: var(--text); }
  .plan { position: absolute; top: 217px; width: 264px; }
  .plan-image { height: 207px; background: radial-gradient(circle at 50% 55%, #b88a55 0%, #c9a77a 22%, var(--card) 48%); }
  .plan-name { margin-top: 14px; font-size: 14.5px; font-weight: 600; color: var(--text); }
  .plan-price { margin-top: 4px; font-size: 20px; font-weight: 700; }

  /* Banner */
  .banner { height: 503px; background: linear-gradient(90deg, #3a3f45 0%, #545a60 35%, #8a7050 62%, #b98a58 80%, #7a5a3c 100%); }
  .banner-text { left: 195px; top: 196px; font-size: 47px; line-height: 43px; font-weight: 600; color: var(--white); }

  /* Split rows */
  .split { height: 401px; display: flex; }
  .split.about { height: 397px; }
  .split .photo { width: 600px; height: 100%; }
  .split .copy { width: 600px; height: 100%; background: var(--panel); position: relative; }
  .photo.box-dog { background: linear-gradient(135deg, #b98a64 0%, #d9b18e 40%, #f2ebe6 55%, #b8885f 100%); }
  .photo.bowl { background: radial-gradient(circle at 40% 55%, #a7834f 0%, #7a5a3a 25%, #6e4427 60%, #532f1a 100%); }
  .copy h2 { position: absolute; font-size: 38px; line-height: 38px; font-weight: 600; }
  .copy p { position: absolute; width: 360px; font-size: 14.5px; line-height: 22.5px; color: var(--text); }
  .btn { position: absolute; display: block; background: var(--ink); color: var(--white); font-size: 19px; text-align: center; text-transform: uppercase; text-decoration: none; }
  .membership h2 { left: 67px; top: 78px; }
  .membership p { left: 67px; top: 170px; }
  .membership .btn { left: 67px; top: 272px; width: 168px; height: 44px; line-height: 44px; }
  .about h2 { left: 172px; top: 78px; }
  .about p { left: 172px; top: 166px; }
  .about .btn { left: 172px; top: 270px; width: 167px; height: 42px; line-height: 42px; }

  /* How it works */
  .how { height: 521px; text-align: center; }
  .how .section-title { position: absolute; top: 62px; width: 100%; }
  .step { position: absolute; top: 150px; width: 230px; }
  .step-icon { height: 122px; display: flex; justify-content: center; align-items: center; }
  .icon-placeholder { width: 124px; height: 120px; border-radius: 12px; background: radial-gradient(circle at 50% 50%, var(--orange) 0%, var(--orange) 45%, var(--orange-soft) 100%); }
  .step h3 { margin-top: 30px; font-size: 19px; font-weight: 700; color: #333; }
  .step p { margin-top: 14px; font-size: 14.5px; line-height: 20px; color: var(--text); }
  .trail { position: absolute; top: 218px; width: 130px; height: 0; border-top: 5px dotted var(--trail); }

  /* Call to action */
  .cta { height: 327px; background: linear-gradient(180deg, #e0531c 0%, #dc5420 60%, #c9521f 100%); text-align: center; color: var(--white); }
  .cta h2 { position: absolute; top: 98px; width: 100%; font-size: 29px; font-weight: 600; }
  .cta p { position: absolute; top: 152px; left: 360px; width: 480px; font-size: 13px; line-height: 17px; }
  .cta .btn { left: 531px; top: 217px; width: 138px; height: 44px; line-height: 44px; font-size: 16px; }

  /* Footer */
  .site-footer { height: 350px; background: var(--footer-bg); color: var(--white); }
  .footer-col { position: absolute; top: 82px; font-size: 12.5px; line-height: 21px; color: var(--muted); }
  .footer-col h4 { font-size: 22px; font-weight: 600; margin-bottom: 16px; color: var(--white); }
  .footer-col ul { list-style: none; }
  .col-links { left: 172px; }
  .col-company { left: 381px; width: 270px; }
  .col-subscribe { left: 732px; width: 300px; }
  .email { position: absolute; left: 732px; top: 178px; width: 258px; height: 38px; background: var(--white); color: #333; font-size: 13px; line-height: 38px; padding-left: 11px; }
  .email-go { position: absolute; left: 990px; top: 178px; width: 37px; height: 38px; background: var(--ink); display: flex; align-items: center; justify-content: center; }
  .footer-rule { position: absolute; left: 179px; top: 273px; width: 844px; height: 1px; background: #555; }
  .copyright { position: absolute; top: 302px; width: 100%; text-align: center; font-size: 13.5px; color: var(--muted); }
  .footer-photo { position: absolute; right: 0; top: 90px; width: 144px; height: 260px; background: linear-gradient(160deg, #2b2b2b 0%, #5a4838 40%, #8b6e50 70%, #3a3029 100%); }
</style>
</head>
<body>

<header class="site-nav">
  <div class="abs brand">Otter Bites Guild</div>
  <ul class="abs menu">
    <li class="active">Home</li>
    <li>Subscription</li>
    <li>How it works</li>
    <li>Contact</li>
  </ul>
  <div class="abs nav-icons" aria-hidden="true">
    <svg width="12" height="14" viewBox="0 0 12 14"><circle cx="5" cy="5.5" r="3.6" fill="none" stroke="#fff" stroke-width="1.8"/><line x1="7.6" y1="8.2" x2="11" y2="11.8" stroke="#fff" stroke-width="2"/></svg>
    <svg width="11" height="14" viewBox="0 0 11 14"><circle cx="5.5" cy="4" r="3" fill="#fff"/><path d="M0.5 13 Q5.5 5 10.5 13 Z" fill="#fff"/></svg>
    <svg width="13" height="14" viewBox="0 0 13 14"><path d="M0 2 H2.5 L4 9 H11 L12.5 4 H3" fill="none" stroke="#fff" stroke-width="1.6"/><circle cx="5" cy="12" r="1.3" fill="#fff"/><circle cx="10" cy="12" r="1.3" fill="#fff"/></svg>
  </div>
</header>

<section class="hero" role="img" aria-label="Photo of a corgi lying on a rug beside a bowl of dog treats">
  <div class="abs hero-title">Otter<br>Bites<br>Guild</div>
  <svg class="abs hero-arrow" style="left:44px" width="22" height="48" viewBox="0 0 22 48" aria-hidden="true"><polyline points="20,2 2,24 20,46" fill="none" stroke="#fff" stroke-width="3"/></svg>
  <svg class="abs hero-arrow" style="left:1124px" width="22" height="48" viewBox="0 0 22 48" aria-hidden="true"><polyline points="2,2 20,24 2,46" fill="none" stroke="#fff" stroke-width="3"/></svg>
</section>

<section class="subscriptions">
  <h2 class="section-title">Monthly Subscriptions</h2>
  <p class="lead">Sed ut perspiciatis unde omnis iste natus error sit voluptatem accusantium doloremque laudantium, totam rem aperiam, eaque ipsa quae ab illo inventore veritatis et quasi architecto beatae vitae dicta sunt</p>
  <div class="plan" style="left:172px">
    <div class="plan-image" role="img" aria-label="Photo of an open cardboard box filled with dog treats"></div>
    <div class="plan-name">Subscription Name</div>
    <div class="plan-price">$250</div>
  </div>
  <div class="plan" style="left:468px">
    <div class="plan-image" role="img" aria-label="Photo of a cardboard box overflowing with kibble"></div>
    <div class="plan-name">Subscription Name</div>
    <div class="plan-price">$250</div>
  </div>
  <div class="plan" style="left:764px">
    <div class="plan-image" role="img" aria-label="Photo of a red gift box holding dog treats"></div>
    <div class="plan-name">Subscription Name</div>
    <div class="plan-price">$250</div>
  </div>
</section>

<section class="banner" role="img" aria-label="Photo of a golden labrador beside a pile of kibble in a living room">
  <div class="abs banner-text">Sed utersiciatis<br>unde omnis iste<br>natuovolu</div>
</section>

<section class="split membership">
  <div class="photo box-dog" role="img" aria-label="Photo of a surprised brown dog looking into a cardboard box"></div>
  <div class="copy">
    <h2>Monthly<br>Membership</h2>
    <p>Sed ut perspiciatis unde omnis iste natus error sit voluptatem accusantium doloremque laudantiutam em aperiam, eaque ipsa quae ab illo inventoreitatis quasi architecto beatae vitae dicta.</p>
    <a class="btn" href="#">Subscribe</a>
  </div>
</section>

<section class="split about">
  <div class="copy">
    <h2>About Otter<br>Bites Guild</h2>
    <p>Sed ut perspiciatis unde omnis iste natus error sit voluptatem accusantium doloremque laudantiutam em aperiam, eaque ipsa quae ab illo inventoreitatis quasi architecto beatae vitae dicta.</p>
    <a class="btn" href="#">Subscribe</a>
  </div>
  <div class="photo bowl" role="img" aria-label="Photo from above of a dog eating kibble from a metal bowl on a wooden floor"></div>
</section>

<section class="how">
  <h2 class="section-title">How It Works</h2>

  <div class="step" style="left:166px">
    <div class="step-icon">
      <div class="icon-placeholder" role="img" aria-label="Orange illustration of a document being signed with a pen"></div>
    </div>
    <h3>1.LOEMPOR</h3>
    <p>Sed ut perspiciatis unde omnis iste natus error sit voluptatem accusantium dolorem</p>
  </div>

  <div class="trail" style="left:376px" aria-hidden="true"></div>

  <div class="step" style="left:486px">
    <div class="step-icon">
      <div class="icon-placeholder" role="img" aria-label="Orange illustration of a taped delivery box"></div>
    </div>
    <h3>2.LSMEMPOR</h3>
    <p>Sed ut perspiciatis unde omnis iste natus error sit voluptatem accusantium dolorem</p>
  </div>

  <div class="trail" style="left:698px" aria-hidden="true"></div>

  <div class="step" style="left:803px">
    <div class="step-icon">
      <div class="icon-placeholder" role="img" aria-label="Orange illustration of a sitting puppy"></div>
    </div>
    <h3>3.SMEMPOR</h3>
    <p>Sed ut perspiciatis unde omnis iste natus error sit voluptatem accusantium dolorem</p>
  </div>
</section>

<section class="cta" role="img" aria-label="Orange-tinted photo of a dog eating from a bowl of kibble">
  <h2>Sed ut perspiciatis unde omnis iste</h2>
  <p>Lorem ipsum dolor sit amet, consectetur adipiscing elit, sed do eiusmod tempor incididunt ut labore et dolore magnLorem ipsum dolor sit amet, consectetur adipiscing elit, sed do eiusmod tpor incididu</p>
  <a class="btn" href="#">Subscribe</a>
</section>

<footer class="site-footer">
  <div class="footer-col col-links">
    <h4>Links</h4>
    <ul>
      <li>Sed ut perloresp</li>
      <li>Aiatis unlormdeo</li>
      <li>Mnis iste narror</li>
      <li>Voluptateaium</li>
      <li>Dolore eunt.</li>
    </ul>
  </div>
  <div class="footer-col col-company">
    <h4>Company</h4>
    <p>Sed ut perspiciatis unde omnis iste na us error sit voluptatem accsan tium dolore mqueunt.Sed ut perspiciatis unde omnis iste na tus error sit voluptatem accsani um doloremqueunt.</p>
  </div>
  <div class="footer-col col-subscribe">
    <h4>Subscribe</h4>
    <p>Sed ut perspiciatis unde omnis iste na tus error sit voluptatem accsan tium doloremqueunt.</p>
  </div>
  <div class="email">Email:</div>
  <div class="email-go" aria-hidden="true">
    <svg width="16" height="10" viewBox="0 0 16 10"><line x1="1" y1="5" x2="14" y2="5" stroke="#fff" stroke-width="1.6"/><polyline points="10,1 14,5 10,9" fill="none" stroke="#fff" stroke-width="1.6"/></svg>
  </div>
  <div class="footer-photo" role="img" aria-label="Photo of a beagle looking upward"></div>
  <div class="footer-rule"></div>
  <div class="copyright">© 2020 Otter Bites Guild. All rights are reserved.</div>
</footer>

</body>
</html>
```